Etiketten für Ätherische Öle, Extrakte und Speiseöle gesucht
Zielgruppe
Wir verkaufen natürlich Produkte. Ätherische öle, Extrakte, Speise öle.
Wir verkaufen im Webshop, Korbix und auch im Betrieb.
https://www.natur-vemo.com
Wir verkaufen hauptsächlich innerhalb Italiens und Deutschland daher doppel sprachig.
Aufgabenstellung
Guten Tag
Bitte verwenden Sie! : * beispiel_10_ml_etikett_nachbau.jpg *
Da mir die kleinste Größe die wichtigste ist habe ich ein beispiel Hochgeladen. Das kleinste Etikett lässt sich öffnen und daher sind nur 7 cm ersichtlich und man muss das Etikett aufmachen.
Habe ein Beispiel Hochgeladen. Aber bitte einfach kreativ sein. *Anhang: beispiel Etikett*
Sobald ich eine Art vom kelinsten habe würde ich dies für die 2 anderen Größen übernehmen aber das man Sie irgendwie gut unterscheiden kann da dies dann komplett andere Produkte (Extrakte/Speise öl) sein werden.
Erstellung von drei unterschiedlichen Größen von Etiketten mit folgenden Eigenschaften:
Am wichtigsten ist mir das kleinste Etikett da dies auch am schwersten ist daher habe ich die anderen Größen nun gelöscht!
• 10 ml Länge: 155 mm Breite: 32 mm.
Brauche 3 unterschiedliche Grund Farben: z. B. Ätherische Öle (Grün) Extrakte (Rot) Speiseöle (gelb). Die Farben lasse ich sie entscheiden.
Die Etiketten müssen 2 Sprachen (Deutsch / Italienisch) sein deshalb muss dieses berücksichtigt werden.
Anbei finden Sie:
• Logo (Bild Logo)
• Beispiel Text ätherische Öle
• Bilder der aktuellen Flaschen
Unter https://www.natur-vemo.com/de finden Sie meine Seite
Anmerkung: Im Anhang: *Back*
Habe ich mein Logo mit Firmennamen ; Bio des Haubner Stefan
Da ich jedoch nicht alle Produkte im biologischen Anbau habe und mein Logo zu miss Verständnis führen könnte habe ich ein Bildliches Logo gemacht das ich fortan auf meinen Produkten haben möchte. Im besonderes dieses Grün das in beiden vorhanden ist versuche ich zu integrieren.
Habe selbst ein Etikett designet das aber sehr unprofessionell wirkt aber dieses Grüne das ich gerne als merkmal unterbringen würde.
Siehe Anhang: neemöl

```html
<!DOCTYPE html>
<html lang="de">
<head>
<meta charset="utf-8">
<title>Lavanda Vera – Etikett 30 ml</title>
<link rel="stylesheet" href="https://fonts.googleapis.com/css2?family=Barlow:wght@400;600&family=Kaushan+Script&display=swap">
<style>
  :root {
    --ink: #2b3a8c;
    --trim: #e6007e;
    --band: #8b0000;
    --paper: #ffffff;
    --black: #111111;
  }
  * { margin: 0; padding: 0; box-sizing: border-box; }
  html, body { width: 1200px; height: 452px; overflow: hidden; background: var(--paper); }
  .label {
    position: relative; width: 1200px; height: 452px;
    font-family: "Barlow", Arial, sans-serif; color: var(--ink);
  }
  .artwork {
    position: absolute; left: 418px; top: 30px; width: 400px; height: 388px;
    background:
      radial-gradient(circle at 48% 42%, rgba(150,110,200,.75) 0, rgba(120,140,220,.55) 22%, rgba(220,190,235,.45) 40%, rgba(255,255,255,0) 62%),
      radial-gradient(ellipse at 50% 92%, rgba(235,240,120,.8) 0, rgba(200,235,150,.5) 30%, rgba(255,255,255,0) 60%),
      #f1f1f3;
  }
  .brand-mark {
    position: absolute; left: 575px; top: 52px; width: 66px; height: 66px;
    background: var(--paper); display: flex; align-items: center; justify-content: center;
    text-align: center; font-size: 12px; font-weight: 600; line-height: 1.1; color: var(--ink);
  }
  .band { position: absolute; top: 316px; height: 42px; background: var(--band); }
  .band--main { left: 22px; width: 873px; }
  .band--end { left: 1131px; width: 69px; }
  .trim-frame { position: absolute; left: 0; top: 0; pointer-events: none; }
  .product-name {
    position: absolute; left: 418px; width: 400px; top: 200px; text-align: center;
    font-family: "Kaushan Script", cursive; font-size: 84px; line-height: 1; color: var(--ink);
  }
  .product-variety {
    position: absolute; left: 566px; top: 284px; width: 92px; height: 30px;
    background: var(--paper); border-radius: 15px; text-align: center;
    font-size: 22px; line-height: 30px; letter-spacing: 9px; padding-left: 9px;
  }
  .volume {
    position: absolute; left: 418px; width: 400px; top: 370px; text-align: center; font-size: 21px;
  }
  .usage {
    position: absolute; left: 47px; top: 53px; width: 340px;
    font-size: 17.5px; line-height: 18.6px;
  }
  .usage strong { font-weight: 600; }
  .company {
    position: absolute; left: 47px; top: 234px; font-size: 8px; line-height: 8.7px;
  }
  .company strong { font-weight: 600; }
  .warnings {
    position: absolute; left: 894px; top: 61px; width: 275px;
    font-size: 18px; line-height: 18.6px;
  }
  .origin { position: absolute; left: 894px; top: 249px; font-size: 18.5px; }
  .best-before { position: absolute; left: 897px; top: 287px; font-size: 12px; color: var(--black); }
</style>
</head>
<body>
<div class="label">
  <div class="artwork" role="img" aria-label="Aquarell-Illustration einer violetten Blüte auf grauem Zickzack-Muster"></div>
  <div class="brand-mark">Natur<br>Vemo</div>

  <div class="band band--main"></div>
  <div class="band band--end"></div>

  <svg class="trim-frame" width="1200" height="452" viewBox="0 0 1200 452" aria-hidden="true">
    <rect x="34" y="29" width="1133" height="378" fill="none" stroke="var(--trim)" stroke-width="2"/>
  </svg>

  <h1 class="product-name">Lavanda</h1>
  <div class="product-variety">Vera</div>
  <div class="volume">30 ml</div>

  <p class="usage">
    100% natürliches etherisches Öl.<br>
    Aroma-Kosmetikum zur Körperpflege.<br>
    <strong>Anwendung:</strong> Als Haut- u. Massageöl<br>
    max 15 Tr. Mit 50 ml z.B. Mandelöl<br>
    mischen.<br>
    Als Badezusatz 8-15 Tr. Auf 4 Eßl. Sahne<br>
    oder Milch ins Badewasser geben.
  </p>

  <address class="company" style="font-style:normal">
    <strong>Firmenname</strong><br>
    Bio des Haubner Stefan<br>
    Lindenweg 14<br>
    I-39099 Talbach<br>
    IVA: IT01234560218<br>
    CF: HBNSTF88M12A952K<br>
    Tel: +39 0471/000123 Handy: 3200001234<br>
    https://www.natur-vemo.com/<br>
    info.naturvemo@mailbox.it
  </address>

  <p class="warnings">
    Nur in der angegeben Ver-<br>
    dünnung anwenden!<br>
    Nicht in die Augen oder auf<br>
    die Schleimhäute<br>
    bringen!<br>
    Außer Reichweite von Kindern<br>
    lagern.
  </p>

  <p class="origin">Abgefüllt in Italien</p>
  <p class="best-before">Mindestens haltbar bis:</p>
</div>
</body>
</html>
```